Banner poster with different motifs

I'm looking for 5 banners and posters in A1 format in the same design, or the similarity must be recognizable...
Kept quite simple with different titles.

1 ballet
2 Contemporary Dance
3 high heels
4 Salsa & Bachata & Zouk
5 Hip Hop

Modern bright colors
it is for the entrance so that the students see here is a dance school

The text may also be included in the image
The photos are for guidance only; some are our own, some are purchased. However, we are permitted to use them, including our logo, of course.

```html
<!DOCTYPE html>
<html lang="en">
<head>
<meta charset="utf-8">
<title>Vivaluz – Contemporary</title>
<link rel="stylesheet" href="https://fonts.googleapis.com/css2?family=Playfair+Display:wght@400&family=Poppins:wght@300;400;600&display=swap">
<style>
  :root {
    --ink-black: #050106;
    --deep-violet: #2a0533;
    --stage-violet: #8a1a9c;
    --glow-magenta: #c23ad6;
    --light-pink: #f3c9ff;
    --letter-grey: #e4dee6;
    --accent-pink: #eaa3f2;
    --white: #ffffff;
  }
  * { margin: 0; padding: 0; box-sizing: border-box; }
  html, body { width: 858px; height: 1200px; overflow: hidden; background: #d6d4d8; }

  .poster {
    position: relative;
    width: 858px;
    height: 1200px;
    overflow: hidden;
    background:
      radial-gradient(ellipse 420px 520px at 410px 760px, rgba(194,58,214,0.85), rgba(138,26,156,0.55) 45%, rgba(42,5,51,0) 80%),
      linear-gradient(180deg, #1a0420 0%, #5a1168 28%, #7c188e 50%, #3d0848 75%, var(--ink-black) 92%);
  }

  .stage {
    position: absolute; inset: 0;
    background:
      radial-gradient(circle 28px at 45px 55px, rgba(255,240,255,0.95), rgba(240,150,255,0.5) 60%, transparent),
      radial-gradient(circle 22px at 110px 68px, rgba(255,240,255,0.9), rgba(240,150,255,0.4) 60%, transparent),
      radial-gradient(circle 26px at 40px 125px, rgba(255,240,255,0.9), rgba(240,150,255,0.4) 60%, transparent),
      radial-gradient(circle 20px at 105px 130px, rgba(255,240,255,0.85), rgba(240,150,255,0.35) 60%, transparent),
      radial-gradient(circle 16px at 160px 95px, rgba(255,240,255,0.8), rgba(240,150,255,0.3) 60%, transparent),
      radial-gradient(circle 30px at 820px 40px, rgba(255,240,255,0.95), rgba(240,150,255,0.5) 60%, transparent),
      radial-gradient(circle 26px at 760px 55px, rgba(255,240,255,0.9), rgba(240,150,255,0.4) 60%, transparent),
      radial-gradient(circle 28px at 815px 120px, rgba(255,240,255,0.9), rgba(240,150,255,0.4) 60%, transparent),
      radial-gradient(circle 20px at 750px 125px, rgba(255,240,255,0.85), rgba(240,150,255,0.35) 60%, transparent),
      radial-gradient(circle 16px at 690px 80px, rgba(255,240,255,0.8), rgba(240,150,255,0.3) 60%, transparent),
      linear-gradient(120deg, transparent 8%, rgba(200,80,220,0.28) 18%, transparent 34%),
      linear-gradient(240deg, transparent 8%, rgba(200,80,220,0.28) 18%, transparent 34%);
  }

  .dancer-photo {
    position: absolute;
    left: 20px; top: 300px;
    width: 740px; height: 720px;
    background:
      radial-gradient(ellipse 180px 90px at 470px 110px, rgba(255,215,235,0.8), transparent 75%),
      radial-gradient(ellipse 120px 260px at 560px 360px, rgba(205,170,220,0.75), transparent 75%),
      radial-gradient(ellipse 170px 130px at 120px 290px, rgba(110,30,60,0.7), transparent 75%),
      radial-gradient(ellipse 60px 110px at 350px 310px, rgba(240,170,215,0.6), transparent 75%);
  }

  .brand {
    position: absolute;
    left: 0; width: 858px; top: 45px;
    display: flex; flex-direction: column; align-items: center;
    color: var(--white);
    font-family: "Poppins", sans-serif;
  }
  .brand-mark {
    width: 84px; height: 84px;
    border: 1.5px solid var(--white);
    border-radius: 50%;
  }
  .brand-name {
    margin-top: 24px;
    font-size: 28px; font-weight: 300;
    letter-spacing: 0.06em;
    line-height: 1;
  }
  .brand-tagline {
    margin-top: 7px;
    font-size: 9px; font-weight: 300;
    letter-spacing: 0.32em;
  }

  .title {
    font-family: "Playfair Display", serif;
    font-weight: 400;
    color: var(--letter-grey);
    line-height: 1;
  }
  .title span { position: absolute; line-height: 1; white-space: nowrap; }
  .word-con { left: 105px; top: 150px; font-size: 300px; letter-spacing: -0.05em; }
  .word-tem { left: 160px; top: 420px; font-size: 222px; letter-spacing: -0.04em; }
  .word-po  { left: 268px; top: 588px; font-size: 236px; letter-spacing: -0.03em; }
  .letter-r1 { left: 80px;  top: 807px; font-size: 222px; }
  .letter-a  { left: 225px; top: 807px; font-size: 222px; }
  .letter-r2 { left: 345px; top: 755px; font-size: 300px; }
  .letter-y  { left: 565px; top: 820px; font-size: 215px; }

  .web-address {
    position: absolute;
    left: 0; width: 858px; top: 1125px;
    text-align: center;
    font-family: "Poppins", sans-serif;
    font-weight: 600;
    font-size: 26px;
    letter-spacing: 0.14em;
    color: var(--white);
  }
  .web-address .domain { color: var(--accent-pink); }
</style>
</head>
<body>
  <main class="poster">
    <div class="stage" role="img" aria-label="Violet stage spotlights shining down from the top corners"></div>
    <div class="dancer-photo" role="img" aria-label="Photo of a dancer in a crop top and loose trousers arching backwards mid-jump, hair flying, lit in violet"></div>

    <header class="brand">
      <div class="brand-mark"></div>
      <div class="brand-name">VIVALUZ</div>
      <div class="brand-tagline">DANCE CENTER FRANKFURT</div>
    </header>

    <h1 class="title" aria-label="Contemporary">
      <span class="word-con">CON</span>
      <span class="word-tem">TEM</span>
      <span class="word-po">PO</span>
      <span class="letter-r1">R</span>
      <span class="letter-a">A</span>
      <span class="letter-r2">R</span>
      <span class="letter-y">Y</span>
    </h1>

    <p class="web-address">www.<span class="domain">vivaluz</span>.de</p>
  </main>
</body>
</html>
```